Luxury Business Card Design for High-End Window Treatments

Gilded Slatworks
Custom Plantation Shutters & Architectural Shading Systems

⸻

BACK

Daniel Trevick
Owner

Custom Interior & Exterior Window Treatments

919-555-0148
gildedslatworks.com

I have included a picture that I’m hoping we can use on the back, but I’m also wondering if you can get rid of the ladder? Should we get rid of shutters , shades and blinds underneath Gilded Slatworks?

Target Market(s)

High-end residential homeowners, custom home builders, architects, interior designers, and luxury renovation clients seeking premium plantation shutters and motorized architectural shading systems.

Industry/Entity Type

Custom Window treatments

Contact Information for Business Card

Front Gilded Slatworks Custom Plantation Shutters Motorized Architectural Shading Systems BACK Daniel Trevick Owner 919-555-0148 GildedSlatworks.com Custom Interior & Exterior Window Treatments By Appointment

Requirements
Nice to have
• Not 100% sure on nice to halves or the color but you can definitely check out my website to get a better understanding of what I’m trying to do

```html
<!DOCTYPE html>
<html lang="en">
<head>
<meta charset="utf-8">
<title>Gilded Slatworks — Business Card</title>
<link rel="stylesheet" href="https://fonts.googleapis.com/css2?family=Prata&family=Poppins:wght@400&display=swap">
<style>
  :root {
    --stage: #1d1d1d;
    --ink: #000000;
    --gold: #c1ab55;
    --gold-bright: #d4bc5c;
    --white: #f4f4f4;
    --photo-dark: #0e1116;
    --photo-mid: #252b33;
  }
  * { box-sizing: border-box; margin: 0; padding: 0; }
  html, body { width: 1200px; height: 1015px; overflow: hidden; }
  body {
    background: var(--stage);
    display: flex;
    flex-direction: column;
    align-items: center;
    justify-content: center;
    gap: 56px;
  }
  .card {
    position: relative;
    width: 600px;
    height: 343px;
    background: var(--ink);
    overflow: hidden;
    box-shadow: 0 12px 30px rgba(0,0,0,.55);
  }

  /* Front */
  .front .brand {
    position: absolute;
    left: 0; right: 0; top: 44px;
    text-align: center;
    font-family: "Prata", serif;
    font-weight: 400;
    color: var(--gold-bright);
    font-size: 54px;
    line-height: 1.02;
    letter-spacing: .5px;
  }
  .front .brand span { display: block; }
  .front .rule-line {
    position: absolute;
    left: 0; right: 0; top: 178px;
    height: 4px;
    background: var(--gold);
  }
  .front .band {
    position: absolute;
    left: 0; right: 0; top: 190px; bottom: 0;
    background: var(--gold);
  }
  .front .tagline {
    position: absolute;
    left: 0; right: 0; top: 204px;
    text-align: center;
    font-family: "Prata", serif;
    color: var(--ink);
    font-size: 19px;
    line-height: 1.35;
  }

  /* Back */
  .back .photo {
    position: absolute;
    right: 0; top: 0; bottom: 0;
    width: 70%;
    background:
      linear-gradient(100deg, var(--ink) 0%, rgba(0,0,0,.85) 22%, rgba(0,0,0,0) 60%),
      linear-gradient(180deg, var(--photo-dark) 0%, var(--photo-mid) 60%, #1a2019 100%);
  }
  .back .details {
    position: absolute;
    left: 56px; top: 104px;
  }
  .back .name {
    font-family: "Prata", serif;
    color: var(--gold-bright);
    font-size: 27px;
    line-height: 1;
  }
  .back .role {
    font-family: "Poppins", sans-serif;
    color: var(--white);
    font-size: 16px;
    margin-top: 2px;
  }
  .back .divider {
    width: 56px;
    height: 1px;
    background: var(--gold);
    margin: 12px 0 14px;
  }
  .back .contact {
    list-style: none;
    font-family: "Poppins", sans-serif;
    color: var(--white);
    font-size: 16px;
    line-height: 1.5;
  }
  .back .contact li { display: flex; align-items: center; gap: 10px; }
  .back .contact svg { width: 16px; height: 16px; fill: var(--gold); flex: none; }
  .back .services {
    font-family: "Prata", serif;
    color: var(--gold);
    font-size: 14.5px;
    line-height: 1.35;
  }
</style>
</head>
<body>

  <section class="card front" aria-label="Card front">
    <h1 class="brand"><span>Gilded</span><span>Slatworks</span></h1>
    <div class="rule-line"></div>
    <div class="band"></div>
    <p class="tagline">Gilded Slatworks Custom<br>Plantation Shutters Motorized<br>Architectural Shading Systems</p>
  </section>

  <section class="card back" aria-label="Card back">
    <div class="photo" role="img" aria-label="Photo of a home's covered porch at dusk with exterior shades lowered"></div>
    <div class="details">
      <h2 class="name">Daniel Trevick</h2>
      <p class="role">Owner</p>
      <div class="divider"></div>
      <ul class="contact">
        <li>
          <svg viewBox="0 0 24 24" aria-hidden="true"><path d="M6.6 10.8a15.1 15.1 0 0 0 6.6 6.6l2.2-2.2a1 1 0 0 1 1-.25 11.4 11.4 0 0 0 3.6.57 1 1 0 0 1 1 1V20a1 1 0 0 1-1 1A17 17 0 0 1 3 4a1 1 0 0 1 1-1h3.5a1 1 0 0 1 1 1c0 1.25.2 2.45.57 3.57a1 1 0 0 1-.25 1z"/></svg>
          919-555-0148
        </li>
        <li>
          <svg viewBox="0 0 24 24" aria-hidden="true"><path d="M2 5h20v14H2zm2 2v.5l8 5 8-5V7l-8 5z"/></svg>
          GildedSlatworks.com
        </li>
      </ul>
      <div class="divider"></div>
      <p class="services">Custom Interior &amp; Exterior<br>Window Treatments By Appointment</p>
    </div>
  </section>

</body>
</html>
```